Wholesale in Gold Jewellery & Gold Bullion

We are an established gold jewellery and gold bullion wholesaler selling these products to international clients. We already have a name and logo of our company, hence please view attached current card design. We need a completely new design to compliment our business and industry and the final design should be new and elegant.

Contact Information for Business Card

New card details must be same as per current card. Like logo, name, tel no. & etc.

Colors

Designer to choose colors to be used in the design.

```html
<!DOCTYPE html>
<html lang="en">
<head>
<meta charset="utf-8">
<title>Vardhan &amp; Co — Business Card</title>
<link rel="stylesheet" href="https://fonts.googleapis.com/css2?family=Libre+Baskerville:wght@700&family=Montserrat:wght@300;400&family=Oswald:wght@500&display=swap">
<style>
  :root {
    --backdrop: #3a3a3a;
    --card: #f7f7f7;
    --gold: #c49a4c;
    --ink: #3d3d3d;
    --muted: #6a6a6a;
  }
  html, body {
    margin: 0;
    width: 1200px;
    height: 897px;
    overflow: hidden;
    background: var(--backdrop);
  }
  .business-card {
    position: absolute;
    left: 150px;
    top: 191px;
    width: 900px;
    height: 514px;
    background: radial-gradient(ellipse at 40% 35%, #ffffff 0%, var(--card) 60%, #ececec 100%);
    box-shadow: 0 18px 40px rgba(0,0,0,.45);
  }
  .brand {
    position: absolute;
    left: 150px;
    top: 120px;
    display: flex;
    align-items: center;
    gap: 22px;
  }
  .brand-dot {
    width: 86px;
    height: 86px;
    border-radius: 50%;
    background: var(--gold);
  }
  .brand-name {
    font-family: "Libre Baskerville", serif;
    font-weight: 700;
    font-size: 26px;
    letter-spacing: 1px;
    color: var(--ink);
  }
  .holder {
    position: absolute;
    left: 150px;
    top: 300px;
    text-align: right;
  }
  .holder-name {
    font-family: "Oswald", sans-serif;
    font-weight: 500;
    font-size: 44px;
    color: var(--gold);
    line-height: 1;
    letter-spacing: .5px;
  }
  .holder-title {
    font-family: "Montserrat", sans-serif;
    font-weight: 300;
    font-size: 26px;
    color: var(--muted);
    margin-top: 4px;
  }
  .divider {
    position: absolute;
    left: 520px;
    top: 232px;
    width: 2px;
    height: 176px;
    background: var(--gold);
  }
  .contact {
    position: absolute;
    left: 556px;
    top: 216px;
    font-family: "Montserrat", sans-serif;
    font-weight: 400;
    font-size: 19px;
    color: var(--muted);
    line-height: 1.35;
  }
  .contact-address { margin: 0 0 14px 0; }
  .contact-list { list-style: none; margin: 0; padding: 0; }
  .contact-list li {
    display: flex;
    align-items: center;
    gap: 14px;
    margin-bottom: 4px;
  }
  .contact-list svg { width: 20px; height: 20px; flex: none; }
</style>
</head>
<body>
  <div class="business-card">
    <div class="brand">
      <div class="brand-dot"></div>
      <div class="brand-name">VARDHAN &amp; CO PTE LTD</div>
    </div>

    <div class="holder">
      <div class="holder-name">ROHAN MEHTANI</div>
      <div class="holder-title">Director</div>
    </div>

    <div class="divider"></div>

    <div class="contact">
      <p class="contact-address">12 Kellock Lane,<br>Singapore 248190</p>
      <ul class="contact-list">
        <li>
          <svg viewBox="0 0 20 20" fill="none" stroke="#c49a4c" stroke-width="1.6"><rect x="5" y="1.5" width="10" height="17" rx="2"/><line x1="9" y1="15.5" x2="11" y2="15.5"/></svg>
          +65 9123 4567
        </li>
        <li>
          <svg viewBox="0 0 20 20" fill="#c49a4c"><path d="M5 2l3 3-2 2.5c1 2.5 3 4.5 5.5 5.5L14 11l3 3-2.5 3C8 16.5 3.5 12 3 4.5z"/></svg>
          +65 6200 1100
        </li>
        <li>
          <svg viewBox="0 0 20 20" fill="#c49a4c"><rect x="5" y="2" width="10" height="6" fill="none" stroke="#c49a4c" stroke-width="1.5"/><rect x="2" y="8" width="16" height="9" rx="1.5"/><rect x="6" y="11" width="8" height="2" fill="#f7f7f7"/></svg>
          +65 6200 1199
        </li>
        <li>
          <svg viewBox="0 0 20 20"><rect x="2" y="4.5" width="16" height="11" fill="#c49a4c"/><path d="M2.5 5l7.5 6 7.5-6" fill="none" stroke="#f7f7f7" stroke-width="1.4"/></svg>
          rohan@vardhanco.com
        </li>
      </ul>
    </div>
  </div>
</body>
</html>
```